Lucky Harbour Fun Casino Entertainment

Looking to update my business card and make it look more modern, stand out and eye catching.
We are are fun casino business in Australia (primarily Sydney). Blackjack and Roulette are our most popular games although we have pretty much every game available for hire that you would find in a real casino. The final design would need to be sleek and appeal to the more upmarket corporate sector.
We mainly cater for Corporate Events, Private Parties, Fundraising Events, Team Building, Poker Tournaments
I think I'd prefer the colour Black.

Target Market(s)

High-end Corporate

Industry/Entity Type

Events

Contact Information for Business Card

Rob Kendall
Director
1300 482 617
0433 728 591
info@luckyharbour.com.au
www.luckyharbour.com.au
Facebook & Instagram @luckyharbourevents (proper social icons preferred)

Colors
000000
0255a3

Requirements
Must have
• Front side:
• Logo
• Contact details
• 'Australia's #1 Fun Casino Specialists'
• Back:
• Logo
Nice to have
• Back:
• Corporate Events
• Private Parties
• Poker Tournaments
• Fundraising
• Props & Theming
• Photo Booth
• Horse Racing Events
• The Vegas Sign attached, maybe on the back of the card in the background...?

```html
<!DOCTYPE html>
<html lang="en">
<head>
<meta charset="utf-8">
<title>Lucky Harbour – Business Card</title>
<link rel="stylesheet" href="https://fonts.googleapis.com/css2?family=Open+Sans:wght@400;700&family=Roboto:wght@400;500&display=swap">
<style>
  :root {
    --stage: #2b2b2b;
    --card: #151515;
    --gold: #f6a623;
    --ink: #ececec;
    --muted: #9c9c9c;
    --rule: #4a4a4a;
  }
  * { box-sizing: border-box; margin: 0; padding: 0; }
  html, body { width: 1200px; height: 782px; overflow: hidden; background: var(--stage); }
  .canvas {
    width: 1200px; height: 782px; position: relative;
    font-family: "Open Sans", Arial, sans-serif;
  }
  .card {
    position: absolute; left: 310px; width: 580px; height: 354px;
    background: var(--card); border-radius: 3px;
    box-shadow: 0 10px 28px rgba(0,0,0,.45);
    overflow: hidden;
  }
  .card--back { top: 26px; }
  .card--front { top: 402px; }

  .brand {
    position: absolute; display: flex; align-items: center; gap: 10px; white-space: nowrap;
  }
  .brand__dot {
    width: 40px; height: 40px; border-radius: 50%; background: var(--gold); flex: none;
  }
  .brand__name {
    font-weight: 700; font-size: 20px; color: var(--gold); letter-spacing: .4px;
    text-transform: uppercase; line-height: 1;
  }

  /* back side */
  .card--back .brand { left: 52px; top: 122px; }
  .tagline {
    position: absolute; left: 40px; top: 214px; white-space: nowrap;
    font-size: 12.5px; color: var(--gold); letter-spacing: .5px; text-transform: uppercase;
  }
  .divider-v {
    position: absolute; width: 1px; background: var(--rule);
  }
  .card--back .divider-v { left: 326px; top: 70px; height: 190px; }
  .services {
    position: absolute; left: 352px; top: 84px; list-style: none;
    font-family: "Roboto", Arial, sans-serif; font-size: 15px; color: var(--ink);
    text-transform: uppercase; letter-spacing: .4px; line-height: 23px; white-space: nowrap;
  }
  .services li { display: flex; align-items: center; gap: 9px; }
  .services li::before {
    content: ""; width: 7px; height: 7px; border-radius: 50%; background: var(--gold); flex: none;
  }

  /* front side */
  .card--front .brand { left: 44px; top: 90px; }
  .divider-h { position: absolute; height: 1px; background: var(--rule); }
  .card--front .divider-h.top { left: 30px; top: 170px; width: 240px; }
  .card--front .divider-h.bottom { left: 330px; top: 318px; width: 220px; }
  .card--front .divider-v { left: 300px; top: 60px; height: 180px; }
  .social {
    position: absolute; left: 30px; width: 240px; top: 194px;
    display: flex; flex-direction: column; align-items: center; gap: 8px;
  }
  .social__icons { display: flex; gap: 6px; }
  .social__icon { width: 18px; height: 18px; border-radius: 50%; background: var(--gold); }
  .social__handle { font-size: 15px; color: var(--ink); letter-spacing: .3px; }

  .person { position: absolute; left: 326px; top: 76px; white-space: nowrap; }
  .person__name {
    font-weight: 700; font-size: 22px; color: var(--gold); text-transform: uppercase; letter-spacing: 1px; line-height: 1.1;
  }
  .person__role { font-size: 14px; color: var(--muted); margin-top: 2px; }
  .contacts { list-style: none; margin-top: 18px; font-size: 15px; color: var(--ink); line-height: 22px; }
  .contacts li { display: flex; align-items: center; gap: 8px; }
  .contacts svg { width: 15px; height: 15px; flex: none; }
</style>
</head>
<body>
<main class="canvas">

  <section class="card card--back" aria-label="Card back">
    <div class="brand">
      <span class="brand__dot"></span>
      <span class="brand__name">Lucky Harbour</span>
    </div>
    <p class="tagline">Australia's #1 Fun Casino Specialists</p>
    <span class="divider-v"></span>
    <ul class="services">
      <li>Corporate Events</li>
      <li>Private Parties</li>
      <li>Poker Tournaments</li>
      <li>Fundraising</li>
      <li>Props &amp; Theming</li>
      <li>Photo Booth</li>
      <li>Horse Racing Events</li>
    </ul>
  </section>

  <section class="card card--front" aria-label="Card front">
    <div class="brand">
      <span class="brand__dot"></span>
      <span class="brand__name">Lucky Harbour</span>
    </div>
    <span class="divider-h top"></span>
    <span class="divider-v"></span>
    <div class="social">
      <div class="social__icons"><span class="social__icon"></span><span class="social__icon"></span></div>
      <span class="social__handle">@luckyharbourevents</span>
    </div>
    <div class="person">
      <h1 class="person__name">Rob Kendall</h1>
      <p class="person__role">Director</p>
      <ul class="contacts">
        <li>
          <svg viewBox="0 0 16 16" aria-hidden="true"><circle cx="8" cy="8" r="8" fill="#f6a623"/><path d="M5 4.5l1.6-.4.9 2-1 .8a5 5 0 0 0 2.6 2.6l.8-1 2 .9-.4 1.6c-3.6.2-6.7-2.9-6.5-6.5z" fill="#151515"/></svg>
          1300 482 617
        </li>
        <li>
          <svg viewBox="0 0 16 16" aria-hidden="true"><circle cx="8" cy="8" r="8" fill="#f6a623"/><rect x="5.5" y="3.5" width="5" height="9" rx="1" fill="#151515"/><rect x="6.5" y="4.8" width="3" height="5.6" fill="#f6a623"/></svg>
          0433 728 591
        </li>
        <li>
          <svg viewBox="0 0 16 16" aria-hidden="true"><circle cx="8" cy="8" r="8" fill="#f6a623"/><rect x="4" y="5" width="8" height="6" fill="#151515"/><path d="M4.3 5.3L8 8.4l3.7-3.1" stroke="#f6a623" stroke-width=".9" fill="none"/></svg>
          info@luckyharbour.com.au
        </li>
        <li>
          <svg viewBox="0 0 16 16" aria-hidden="true"><circle cx="8" cy="8" r="8" fill="#f6a623"/><circle cx="8" cy="8" r="4.2" fill="none" stroke="#151515" stroke-width="1.1"/><path d="M3.8 8h8.4M8 3.8c-2 2.4-2 6 0 8.4M8 3.8c2 2.4 2 6 0 8.4" stroke="#151515" stroke-width=".9" fill="none"/></svg>
          www.luckyharbour.com.au
        </li>
      </ul>
    </div>
    <span class="divider-h bottom"></span>
  </section>

</main>
</body>
</html>
```